Veldmark Supplies Business Card

Professional business card that stand out to our potential customers. Front and back with clean modern design

Industry/Entity Type

Oil and gas

Contact Information for Business Card

Name, address, website , office phone and cell number

Requirements
Must have
• Editable files for each employee

```html
<!DOCTYPE html>
<html lang="en">
<head>
<meta charset="utf-8">
<title>Veldmark Supplies – Business Card</title>
<link rel="stylesheet" href="https://fonts.googleapis.com/css2?family=Lato:wght@400;700;900&display=swap">
<style>
  :root {
    --bg: #141414;
    --card: #1e1e1e;
    --red: #f2121b;
    --blue: #10b4d8;
    --text: #d6d6d6;
    --muted: #bdbdbd;
  }
  * { margin: 0; padding: 0; box-sizing: border-box; }
  html, body {
    width: 1200px; height: 801px; overflow: hidden;
    background: radial-gradient(circle at 50% 50%, #2b2b2b 0%, var(--bg) 75%);
    font-family: "Lato", sans-serif;
  }
  .stage {
    width: 1200px; height: 801px;
    display: flex; align-items: center; justify-content: center; gap: 40px;
  }
  .card {
    width: 540px; height: 309px;
    background: var(--card);
    border-radius: 16px;
    position: relative;
    box-shadow: 0 18px 40px rgba(0,0,0,.55);
  }
  .card-front { display: flex; align-items: center; justify-content: center; }
  .brand-front {
    display: flex; align-items: center; gap: 14px;
    color: var(--red); font-weight: 900; font-size: 30px; letter-spacing: 1px;
    text-transform: uppercase;
  }
  .brand-mark { width: 22px; height: 22px; background: var(--red); }

  .card-back { padding: 40px 36px 0 36px; }
  .brand-back {
    color: var(--red); font-weight: 900; font-size: 34px; letter-spacing: 1px;
    text-transform: uppercase; text-align: center; margin-bottom: 42px;
  }
  .details { display: flex; align-items: stretch; gap: 26px; justify-content: center; }
  .person { text-align: right; }
  .person-name { color: var(--red); font-weight: 700; font-size: 22px; text-transform: uppercase; line-height: 1.1; }
  .person-title { color: var(--blue); font-size: 15px; margin-bottom: 8px; }
  .person-address { color: var(--muted); font-size: 13px; line-height: 1.45; }
  .divider { width: 2px; background: var(--blue); }
  .contact-list { list-style: none; color: var(--text); font-size: 13px; line-height: 1.7; }
  .contact-list li { display: flex; align-items: center; gap: 9px; }
  .contact-list svg { width: 12px; height: 12px; fill: var(--red); flex: none; }
</style>
</head>
<body>
<main class="stage">
  <section class="card card-front" aria-label="Card front">
    <div class="brand-front"><span class="brand-mark"></span>Veldmark Supplies</div>
  </section>

  <section class="card card-back" aria-label="Card back">
    <div class="brand-back">Veldmark Supplies</div>
    <div class="details">
      <div class="person">
        <p class="person-name">Daniel Reyes</p>
        <p class="person-title">Founder &amp; CEO</p>
        <p class="person-address">Veldmark Supplies Group<br>423 Street Address Here, City<br>State &amp; Country, ZIP Code</p>
      </div>
      <div class="divider"></div>
      <ul class="contact-list">
        <li><svg viewBox="0 0 24 24"><path d="M6.6 10.8a15.1 15.1 0 0 0 6.6 6.6l2.2-2.2c.3-.3.7-.4 1-.2 1.1.4 2.3.6 3.6.6.6 0 1 .4 1 1V20c0 .6-.4 1-1 1A17 17 0 0 1 3 4c0-.6.4-1 1-1h3.5c.6 0 1 .4 1 1 0 1.3.2 2.5.6 3.6.1.3 0 .7-.2 1z"/></svg>(123) 456-7890</li>
        <li><svg viewBox="0 0 24 24"><path d="M7 1h10a2 2 0 0 1 2 2v18a2 2 0 0 1-2 2H7a2 2 0 0 1-2-2V3a2 2 0 0 1 2-2zm0 3v14h10V4zm5 15.5a1 1 0 1 0 0 2 1 1 0 0 0 0-2z"/></svg>(123) 456-7890</li>
        <li><svg viewBox="0 0 24 24"><path d="M6 2h12v5H6zM4 8h16a2 2 0 0 1 2 2v7h-4v5H6v-5H2v-7a2 2 0 0 1 2-2zm4 8v4h8v-4z"/></svg>(123) 456-7890</li>
        <li><svg viewBox="0 0 24 24"><path d="M2 5h20v14H2zm2 2v.5l8 5 8-5V7z"/></svg>info@yourwebsitehere.com</li>
        <li><svg viewBox="0 0 24 24"><path d="M12 2a10 10 0 1 0 0 20 10 10 0 0 0 0-20zm0 2c1 1.3 1.8 3 2.2 5H9.8C10.2 7 11 5.3 12 4zM4.3 11h3.5a16 16 0 0 0 0 2H4.3a8 8 0 0 1 0-2zm5.5 0h4.4a14 14 0 0 1 0 2H9.8a14 14 0 0 1 0-2zm6.4 0h3.5a8 8 0 0 1 0 2h-3.5a16 16 0 0 0 0-2zM9.8 15h4.4c-.4 2-1.2 3.7-2.2 5-1-1.3-1.8-3-2.2-5z"/></svg>yourwebsitehere.com</li>
      </ul>
    </div>
  </section>
</main>
</body>
</html>
```